Stonebridge Building and Projects business cards

A business card with watermark background (construction work)

Company logo attached

Home improvement projects
House renovations
Bathroom and kitchen renovations
House extensions
New builds and granny flats

Director Omar Haddani
(Phone number)
omar@sbpbuilding.com.au
(Instagram logo) sbp_building

```html
<!DOCTYPE html>
<html lang="en">
<head>
<meta charset="utf-8">
<title>Stonebridge Building and Projects – Business Cards</title>
<link rel="stylesheet" href="https://fonts.googleapis.com/css2?family=Montserrat:wght@600&family=Raleway:wght@700&family=Arimo:wght@400&display=swap">
<style>
  :root {
    --brand-blue: #2e74b5;
    --brand-blue-deep: #2a6cab;
    --ink: #333333;
    --rule: #8a8a8a;
    --paper: #ffffff;
    --backdrop: #d9d9d9;
  }
  * { box-sizing: border-box; margin: 0; padding: 0; }
  html, body { width: 1200px; height: 1200px; overflow: hidden; }
  body {
    background: var(--backdrop);
    position: relative;
    font-family: "Arimo", Arial, sans-serif;
  }
  .card {
    position: absolute;
    top: 303px;
    width: 369px;
    height: 594px;
    text-align: center;
  }
  .card--front { left: 201px; color: var(--paper); }
  .card--back { left: 599px; width: 365px; background: var(--paper); color: var(--ink); }

  .card__watermark {
    position: absolute; inset: 0;
    background: linear-gradient(160deg, #3279bb 0%, var(--brand-blue) 50%, var(--brand-blue-deep) 100%);
  }

  .wordmark {
    position: absolute; left: 0; right: 0;
    font-family: "Montserrat", sans-serif;
    font-weight: 600;
    line-height: 1.15;
  }
  .card--front .wordmark { top: 230px; font-size: 27px; color: var(--paper); }
  .card--back .wordmark { top: 150px; font-size: 27px; color: var(--brand-blue); }
  .wordmark__square {
    display: block; width: 40px; height: 40px;
    margin: 0 auto 18px; background: var(--brand-blue);
  }

  .services {
    position: absolute; left: 0; right: 0; top: 455px;
    list-style: none;
    font-size: 17px; line-height: 21.5px;
  }

  .person { position: absolute; left: 0; right: 0; top: 333px; }
  .person__name {
    font-family: "Raleway", sans-serif; font-weight: 700;
    font-size: 25px; color: var(--brand-blue); line-height: 1.2;
  }
  .person__role { font-size: 16px; margin-top: 2px; }

  .icon-row {
    position: absolute; left: 0; right: 0;
    display: flex; align-items: center; justify-content: center; gap: 4px;
  }
  .icon-row--contact { top: 396px; }
  .icon-row--social { top: 506px; }
  .icon-row__rule { width: 33px; height: 1px; background: var(--rule); margin: 0 3px; }
  .icon-row--social .icon-row__rule { width: 60px; margin: 0 8px; }
  .icon {
    width: 25px; height: 25px; border-radius: 3px;
    background: var(--brand-blue);
    display: flex; align-items: center; justify-content: center;
  }
  .icon--plain { width: 21px; height: 21px; border-radius: 4px; }

  .contacts {
    position: absolute; left: 0; right: 0; top: 427px;
    font-size: 17px; line-height: 21.8px;
  }
  .contacts__highlight { color: var(--brand-blue); }
  .social-handle { position: absolute; left: 0; right: 0; top: 539px; font-size: 17px; }
</style>
</head>
<body>

  <section class="card card--front">
    <div class="card__watermark" role="img" aria-label="Faint construction-work watermark over the blue card background"></div>
    <div class="wordmark">Stonebridge<br>Building and Projects</div>
    <ul class="services">
      <li>Home improvement projects</li>
      <li>House renovations</li>
      <li>Bathroom and kitchen renovations</li>
      <li>House extensions</li>
      <li>New builds and granny flats</li>
    </ul>
  </section>

  <section class="card card--back">
    <div class="wordmark"><span class="wordmark__square"></span>Stonebridge<br>Building and Projects</div>

    <div class="person">
      <div class="person__name">Omar Haddani</div>
      <div class="person__role">Director</div>
    </div>

    <div class="icon-row icon-row--contact">
      <span class="icon-row__rule"></span>
      <span class="icon" aria-label="Phone">
        <svg width="17" height="13" viewBox="0 0 17 13"><path d="M1 4 Q8.5 -1 16 4 L14 6 L11.5 4.5 L11.5 3 Q8.5 2 5.5 3 L5.5 4.5 L3 6 Z M4 7 L13 7 L14 12 L3 12 Z" fill="#fff"/></svg>
      </span>
      <span class="icon" aria-label="Email">
        <svg width="17" height="12" viewBox="0 0 17 12"><rect x="0.7" y="0.7" width="15.6" height="10.6" fill="none" stroke="#fff" stroke-width="1.3"/><path d="M1 1 L8.5 7 L16 1 M1 11 L6.5 5.5 M16 11 L10.5 5.5" fill="none" stroke="#fff" stroke-width="1.2"/></svg>
      </span>
      <span class="icon" aria-label="Website">
        <svg width="16" height="16" viewBox="0 0 16 16"><circle cx="8" cy="8" r="7" fill="none" stroke="#fff" stroke-width="1.4"/><ellipse cx="8" cy="8" rx="3" ry="7" fill="none" stroke="#fff" stroke-width="1.1"/><path d="M1 8 H15" stroke="#fff" stroke-width="1.1"/></svg>
      </span>
      <span class="icon-row__rule"></span>
    </div>

    <div class="contacts">
      <div>044-987 654 321</div>
      <div>omar@sbpbuilding.com.au</div>
      <div>www.<span class="contacts__highlight">sbpbuilding</span>.com.au</div>
    </div>

    <div class="icon-row icon-row--social">
      <span class="icon-row__rule"></span>
      <span class="icon icon--plain" aria-label="Social media"></span>
      <span class="icon-row__rule"></span>
    </div>
    <div class="social-handle">sbp_building</div>
  </section>

</body>
</html>
```